Inspirational music needs a cd cover design

This CD is an individual project (no company). It is meant to reach
as many people as possible with great, inspiring music. It will be
available by mail and at gigs.

The cover will be a 4-panel eco-wallet (front cover, back cover, left
and right inside panels). I have a template from the CD manufacturing
company.

Target Market(s)

I am aiming for a very broad market. That said, the median age will
likely be 40 years old, and the CD will particularly appeal to people
concerned about climate change and activism, especially in the U.S.

Industry/Entity Type

It Company

Colors

Designer to choose colors to be used in the design.

Requirements
Must have
• I have an image that I would like on the front cover, and on the CD
• itself. It is a photo of a painting. I also have a photo of me for the back cover. For the background on the inner 2 panels I don't have an image but would like an image of a sky with storm clouds as long as the text is clearly readable.
• Typefaces: For the informational text I'd like something easy to read, like Verdana. For the album title and my name on the front cover, two typeface examples I like are the cover of Colin Prewett Band "Beside Cold Rivers Slowly Waking" and Gordon Pelsky and Lanternfall "Hum Tide."

```html
<!DOCTYPE html>
<html lang="en">
<head>
<meta charset="utf-8">
<title>Inside Panels – Credits and Benediction</title>
<link rel="stylesheet" href="https://fonts.googleapis.com/css2?family=Nunito+Sans:ital,wght@0,400;0,700;1,400&display=swap">
<style>
  :root {
    --sheet: #ffffff;
    --storm-dark: #2f2f2c;
    --storm-mid: #56554f;
    --storm-light: #8a877c;
    --sky-pale: #ebe6d8;
    --sky-warm: #d6cfbc;
    --cloud-grey: #6f6c63;
    --ink-light: #ffffff;
    --ink-dark: #1b1b19;
  }
  * { box-sizing: border-box; margin: 0; padding: 0; }
  html, body { width: 1200px; height: 534px; overflow: hidden; background: var(--sheet); }
  .spread {
    position: relative;
    width: 1200px; height: 534px;
    font-family: "Nunito Sans", sans-serif;
  }
  .panel { position: absolute; top: 0; height: 534px; overflow: hidden; }
  .panel--credits { left: 0; width: 597px; }
  .panel--benediction { left: 612px; width: 588px; }
  .sky { position: absolute; inset: 0; }
  .sky--storm {
    background:
      radial-gradient(ellipse 70% 45% at 30% 35%, var(--storm-dark) 0%, transparent 75%),
      radial-gradient(ellipse 60% 40% at 80% 60%, var(--storm-mid) 0%, transparent 80%),
      linear-gradient(180deg, var(--storm-mid) 0%, var(--storm-dark) 45%, var(--storm-mid) 78%, var(--storm-light) 90%, var(--sky-warm) 100%);
  }
  .sky--clearing {
    background:
      radial-gradient(ellipse 40% 35% at 18% 35%, var(--storm-dark) 0%, transparent 80%),
      radial-gradient(ellipse 75% 30% at 55% 70%, var(--cloud-grey) 0%, transparent 75%),
      radial-gradient(ellipse 50% 28% at 38% 10%, var(--storm-mid) 0%, transparent 80%),
      linear-gradient(180deg, var(--sky-warm) 0%, var(--sky-pale) 35%, var(--sky-warm) 80%, var(--sky-pale) 100%);
  }
  .credits {
    position: absolute; left: 27px; top: 46px; width: 566px;
    color: var(--ink-light);
    font-size: 11.6px; line-height: 14.6px;
  }
  .credits p + p { margin-top: 14.6px; }
  .credits .track { font-weight: 700; }
  .benediction {
    position: absolute; left: 124px; top: 49px; width: 500px;
    text-align: center; color: var(--ink-dark);
    font-size: 11.1px; line-height: 14.7px;
  }
  .benediction h2 { font-size: 14.4px; line-height: 20px; font-weight: 700; margin-bottom: 12px; }
  .benediction .stanza + .stanza { margin-top: 14.7px; }
  .benediction .stanza--fear { font-style: italic; }
  .fold { position: absolute; left: 0; top: 0; width: 1200px; height: 534px; pointer-events: none; }
</style>
</head>
<body>
<main class="spread">
  <section class="panel panel--credits">
    <div class="sky sky--storm" role="img" aria-label="Photograph of a dark stormy sky with heavy grey clouds"></div>
    <div class="credits">
      <p>All lead vocals, keyboards, acoustic guitar, and arranging ML except where noted.<br>
      All drums and percussion Kieran Dell.<br>
      <span class="track">The Song of Will Hartigan:</span> backing vocals DK, GS/ organ DK/ saxophones and horn arr.<br>
      Alma Stroud/ trumpets Reuben Kessler, Joel Carrick/ bass EF/ additional arranging DK.<br>
      <span class="track">Other Horizons:</span> backing vocals JA, SD/ bass EF/ violin Tamsin Leigh/ vocal arr. JA.<br>
      <span class="track">Ray’s Starlit Trading Post:</span> backing vocals ML/ bass DR.<br>
      <span class="track">Luminous:</span> backing vocals TB, JA/ bass DR/ cello Boyd Pemberton/ vocal arr. JA.<br>
      <span class="track">The Verdant Tycoon:</span> backing vocals JA, ML/ bass EF/ elec. guitar DC/<br>
      “not an activist” Ray Lombardo/ vocal arr. JA, ML.<br>
      <span class="track">Four Doorways:</span> backing vocals GS/ elec. guitar DK/ bass EF/ “biggering” The Grabbler/<br>
      “the world will end” Lena Hargrove/ other voices by real capitalists/ additional arranging DK.<br>
      <span class="track">Homo Habilis:</span> backing vocals ML/ bass EF/ elec. guitar TC.<br>
      <span class="track">Standfast:</span> backing vocals JA, SD, ML/ vocal and synth arranging JA.<br>
      <span class="track">Miriam’s Eyes:</span> backing vocals JA, GS, ML/ bass EF/ elec. guitar TC/ glockenspiel JA/ vocal arr. JA.<br>
      <span class="track">Rise Now:</span> vocals TB, ML, JA/ elec. guitar DC/ bass EF/ vocal arr. JA.<br>
      <span class="track">Come Walk Beside Me:</span> backing vocals JA, SD/ bass EF/ saxes Glen Rosario/ vocal arr. JA.</p>
      <p>DC: Derek Calloway DK: Dorian Kell DR: Del Rourke EF: Emile Fontaine GS: Greta Sorell JA: Jonah<br>
      Ashby SD: Selma Dorn TB: Tessa Bright TC: Tobias Crane.</p>
      <p>All tracks recorded and mixed at Lowtide Studio, Aptos, CA by Sam Whitlow with production assistance<br>
      from JA except #1 and #6 at Fernhollow Studio, Santa Cruz, CA by Julian Marsh assisted by DK.<br>
      Mastered by Roland Gessner at Ochre Digital.<br>
      Cover art Adrian Pollard, Photo Rowan Dempsey, Layout Walt Merrin.</p>
      <p>Great big love to Sam and Jonah for their extraordinary giving of themselves,<br>
      to Juliet for seeing the possible, and always to Bettina.<br>
      And special gratitude to Brent Gaskell and Dean Lowry for their support.</p>
    </div>
  </section>

  <section class="panel panel--benediction">
    <div class="sky sky--clearing" role="img" aria-label="Photograph of a pale sky with a dark storm cloud drifting across"></div>
    <div class="benediction">
      <h2>Benediction</h2>
      <p class="stanza stanza--fear">The weather takes a turn to Fear.<br>
      Things are gray.<br>
      We sit in a little room, and stare at a little screen.<br>
      Drudgery, addiction, criticism, denial, automation:<br>
      The accompanists of Fear’s silent song.<br>
      The dry dust in our mouth tastes of impossibility.</p>
      <p class="stanza">Love returns like water trickling into parched earth.<br>
      Places that seemed dead come to life again.<br>
      Hard ground relaxes, green things appear,<br>
      birds arrive from somewhere and speak in music,<br>
      and the land smiles and says, “I Remember!”</p>
      <p class="stanza">To whoever reads this and whoever writes this:<br>
      May Love always return to you.<br>
      May the warm rain of Love water all that is parched in you;<br>
      may your prisoners all be set free;<br>
      may your ample corridors echo again with laughter and song;<br>
      may the wide world again beckon you outside to dance;<br>
      may Yes bloom magnificently and give a resting place to No;<br>
      may the moonrise shock you with its beauty;<br>
      may you remember now all that Fear once forgot.</p>
    </div>
  </section>

  <svg class="fold" viewBox="0 0 1200 534" aria-hidden="true">
    <rect x="597" y="0" width="15" height="534" fill="var(--sheet)"/>
    <path d="M612,112 C612,190 640,228 704,228 L722,228 Q758,228 758,264 L758,272 Q758,308 722,308 L636,308 Q612,308 612,336 Z" fill="var(--sheet)"/>
  </svg>
</main>
</body>
</html>
```